SkyvornQ Business Cards and Stationary Design

Need a design for our business cards and stationary. I want to carry on the theme of the logo. I want the business cards to have a design on the back. I would like the business cards and the stationary to carry the same theme, design scheme, and branding

Target Market(s)

Airlines and Maintenance Facilities

Industry/Entity Type

Aviation

Contact Information for Business Card

Name
Position Title
Address: 4827 Trellis Hollow Road, Fort Pierce, Florida, 34951
Office Number
Mobile Number
Email
Website

Font styles to use
Serif
Sans Serif

Colors

Designer to choose colors to be used in the design.

```html
<!DOCTYPE html>
<html lang="en">
<head>
<meta charset="utf-8">
<title>SkyvornQ Business Card</title>
<link href="https://fonts.googleapis.com/css2?family=Roboto:wght@400;700&display=swap" rel="stylesheet">
<style>
  :root {
    --backdrop: #e2e2e2;
    --paper: #f6f6f6;
    --navy: #0d2b55;
    --navy-deep: #041a38;
    --sky: #1aa0e8;
    --brand-blue: #0e4fa3;
    --ink: #555a60;
    --ink-light: #4a4d52;
  }
  * { margin: 0; padding: 0; box-sizing: border-box; }
  html, body {
    width: 1200px; height: 960px; overflow: hidden;
    background: var(--backdrop);
    font-family: "Roboto", Arial, sans-serif;
  }
  .canvas { position: relative; width: 1200px; height: 960px; }

  .card {
    position: absolute;
    background: var(--paper);
    overflow: hidden;
  }
  .card--front { left: 315px; top: 113px; width: 598px; height: 342px; }
  .card--back  { left: 311px; top: 472px; width: 600px; height: 342px; }

  .front__band {
    position: absolute; right: 0; top: 0;
    width: 163px; height: 100%;
    background: var(--navy-deep);
  }
  .front__emblem {
    position: absolute; left: 218px; top: 0;
    width: 344px; height: 344px; border-radius: 50%;
    background: linear-gradient(135deg, var(--sky) 0%, var(--brand-blue) 55%, var(--navy) 100%);
  }
  .front__marker {
    position: absolute; left: 0; top: 144px;
    width: 15px; height: 43px;
    background: var(--navy-deep);
  }
  .contact { position: absolute; left: 28px; top: 144px; }
  .contact__name {
    font-size: 21px; font-weight: 700; color: var(--navy);
    line-height: 26px; letter-spacing: 0.01em;
  }
  .contact__role {
    font-size: 15.5px; font-weight: 400; color: var(--sky);
    line-height: 19px; margin-bottom: 8px;
  }
  .contact__address {
    font-size: 15px; color: var(--ink); line-height: 18px;
    font-style: normal; margin-bottom: 10px;
  }
  .contact__list { list-style: none; }
  .contact__item {
    display: flex; align-items: center;
    font-size: 15px; color: var(--ink); line-height: 19px;
  }
  .contact__icon {
    width: 13px; height: 13px; margin-right: 10px; flex: none;
    fill: var(--navy);
  }

  .back__dot {
    position: absolute; left: 246px; top: 100px;
    width: 86px; height: 86px; border-radius: 50%;
    background: var(--brand-blue);
  }
  .back__name {
    position: absolute; left: 0; top: 197px; width: 100%;
    text-align: center; padding-left: 0.22em;
    font-size: 32px; font-weight: 700; color: var(--navy);
    letter-spacing: 0.22em;
  }
  .back__web {
    position: absolute; left: 0; top: 290px; width: 100%;
    text-align: center; padding-left: 0.6em;
    font-size: 14px; color: var(--ink-light);
    letter-spacing: 0.6em;
  }
</style>
</head>
<body>
<main class="canvas">

  <section class="card card--front" aria-label="Business card front">
    <div class="front__band"></div>
    <div class="front__emblem" role="img" aria-label="Large brand emblem in blue gradient"></div>
    <div class="front__marker"></div>
    <div class="contact">
      <h1 class="contact__name">DANA MERCER</h1>
      <p class="contact__role">CEO/FOUNDER</p>
      <address class="contact__address">4827 Trellis Hollow Road<br>Fort Pierce, Florida, 34951</address>
      <ul class="contact__list">
        <li class="contact__item">
          <svg class="contact__icon" viewBox="0 0 24 24"><path d="M6.6 10.8a15.1 15.1 0 0 0 6.6 6.6l2.2-2.2c.3-.3.7-.4 1-.2 1.1.4 2.3.6 3.6.6.6 0 1 .4 1 1V20c0 .6-.4 1-1 1A17 17 0 0 1 3 4c0-.6.4-1 1-1h3.5c.6 0 1 .4 1 1 0 1.3.2 2.5.6 3.6.1.3 0 .7-.2 1z"/></svg>
          772 310 4186
        </li>
        <li class="contact__item">
          <svg class="contact__icon" viewBox="0 0 24 24"><path d="M7 1h10a2 2 0 0 1 2 2v18a2 2 0 0 1-2 2H7a2 2 0 0 1-2-2V3a2 2 0 0 1 2-2zm0 3v14h10V4zm5 15.5a1.2 1.2 0 1 0 0 2.4 1.2 1.2 0 0 0 0-2.4z"/></svg>
          772 594 2071
        </li>
        <li class="contact__item">
          <svg class="contact__icon" viewBox="0 0 24 24"><path d="M2 5h20v14H2zm2 2v.5l8 5 8-5V7zm0 2.8V17h16V9.8l-8 5z"/></svg>
          info@skyvornq.com
        </li>
        <li class="contact__item">
          <svg class="contact__icon" viewBox="0 0 24 24"><path d="M12 2a10 10 0 1 0 0 20 10 10 0 0 0 0-20zm-1 17.9A8 8 0 0 1 4.2 10.2L9 15v1a2 2 0 0 0 2 2zm6.9-2.5A2 2 0 0 0 16 16h-1v-3a1 1 0 0 0-1-1H8v-2h2a1 1 0 0 0 1-1V7h2a2 2 0 0 0 2-2v-.4a8 8 0 0 1 2.9 12.8z"/></svg>
          www.skyvornq.com
        </li>
      </ul>
    </div>
  </section>

  <section class="card card--back" aria-label="Business card back">
    <div class="back__dot"></div>
    <p class="back__name">SKYVORNQ</p>
    <p class="back__web">www.skyvornq.com</p>
  </section>

</main>
</body>
</html>
```